Home Security Company Business Card

Looking for a eye catching business card that is non traditional and stands out but yet still looks professional. It should include all the pertinent information such as name, title, address, telephone, e-mail, website address should definitely stand out and then finally the logo.

Target Market(s)

Residential and Commercial accounts mostly upscale accounts

Industry/Entity Type

Security

Contact Information for Business Card

Name
Title
Address
Office #
Cell #
E-mail
Website

Font styles to use
Serif
Sans Serif

Requirements
Must have
• Logo, two sided color configuration
Nice to have
• You decide
Should not have
• There really aren't any.

```html
<!DOCTYPE html>
<html lang="en">
<head>
<meta charset="utf-8">
<title>Ironhold Security Systems – Business Card</title>
<link href="https://fonts.googleapis.com/css2?family=Open+Sans:wght@400;700&display=swap" rel="stylesheet">
<style>
  :root {
    --backdrop: #e9e4df;
    --card-top: #a73440;
    --card-bottom: #6b0e16;
    --gold: #e3b04a;
    --gold-deep: #c8902c;
    --white: #ffffff;
    --soft-white: #f3e7e8;
  }
  * { box-sizing: border-box; margin: 0; padding: 0; }
  html, body {
    width: 1200px; height: 913px; overflow: hidden;
    background: var(--backdrop);
    font-family: "Open Sans", Arial, sans-serif;
  }
  .stage {
    width: 1200px; height: 913px;
    display: flex; align-items: center; justify-content: center; gap: 40px;
  }
  .card {
    position: relative;
    width: 540px; height: 309px;
    border-radius: 4px;
    background: linear-gradient(160deg, var(--card-top) 0%, #8c1d28 50%, var(--card-bottom) 100%);
    box-shadow: 0 14px 30px rgba(60, 10, 15, 0.35);
    overflow: hidden;
    color: var(--white);
  }
  .brand {
    position: absolute;
    display: flex; align-items: center; gap: 12px;
  }
  .brand-dot {
    width: 52px; height: 52px; border-radius: 50%;
    background: var(--gold);
    flex: none;
  }
  .brand-name {
    font-family: "Open Sans", Arial, sans-serif;
    font-weight: 700;
    font-size: 16px;
    color: var(--white);
    white-space: nowrap;
  }

  /* front */
  .card-front .brand { left: 170px; top: 52px; }
  .edge-tab {
    position: absolute; left: -22px; top: 176px;
    width: 44px; height: 44px; border-radius: 50%;
    background: var(--gold);
  }
  .name-row {
    position: absolute; left: 40px; right: 32px; top: 134px;
    display: flex; align-items: flex-end; gap: 8px;
  }
  .person-name { font-size: 22px; font-weight: 700; line-height: 1; white-space: nowrap; }
  .rule { flex: 1; height: 1.5px; background: var(--white); margin-bottom: 3px; }
  .person-title { position: absolute; left: 40px; top: 160px; font-size: 13px; color: var(--gold); }
  .address { position: absolute; left: 40px; top: 200px; font-size: 14px; line-height: 20px; color: var(--soft-white); }
  .contacts {
    position: absolute; right: 32px; top: 164px;
    font-size: 13px; line-height: 19px;
  }
  .contacts li { list-style: none; display: flex; justify-content: flex-end; align-items: center; gap: 8px; }
  .contacts svg { width: 12px; height: 12px; fill: none; stroke: var(--gold); stroke-width: 1.6; }
  .contacts .email { margin-top: 40px; }

  /* back */
  .card-back .brand { left: 150px; top: 92px; }
  .card-back .brand-dot { width: 68px; height: 68px; }
  .card-back .brand-name { font-size: 19px; }
  .website {
    position: absolute; left: 90px; top: 198px;
    font-size: 15px; font-weight: 700; letter-spacing: 0.3px;
  }
  .gold-rule { position: absolute; left: 70px; right: 40px; top: 230px; height: 1.5px; background: var(--gold-deep); }
</style>
</head>
<body>
<main class="stage">
  <section class="card card-front" aria-label="Business card front">
    <div class="edge-tab"></div>
    <div class="brand">
      <span class="brand-dot"></span>
      <span class="brand-name">Ironhold Security Systems Inc.</span>
    </div>
    <div class="name-row">
      <span class="person-name">Daniel Hartwell</span>
      <span class="rule"></span>
    </div>
    <p class="person-title">Owner</p>
    <p class="address">742 Maple Avenue<br>Fairview, Illinois 60199</p>
    <ul class="contacts">
      <li>+330 5550-1842
        <svg viewBox="0 0 12 12"><path d="M1.5 5 Q6 1 10.5 5 L9 6.5 L7.5 5.5 L4.5 5.5 L3 6.5 Z"/><rect x="3.5" y="7" width="5" height="3.5" rx="0.5"/></svg></li>
      <li>+3305550-27314
        <svg viewBox="0 0 12 12"><path d="M3 1.5 L5 1.5 L5.5 4 L4.3 4.8 Q5.2 7 7.2 7.7 L8 6.5 L10.5 7 L10.5 9 Q10 10.5 8.5 10.5 Q2 9.5 1.5 3.5 Q1.5 2 3 1.5 Z"/></svg></li>
      <li class="email">info@danielhartwellmail.com
        <svg viewBox="0 0 12 12"><rect x="1" y="2.5" width="10" height="7" rx="0.8"/><path d="M1.5 3 L6 6.8 L10.5 3"/></svg></li>
    </ul>
  </section>

  <section class="card card-back" aria-label="Business card back">
    <div class="brand">
      <span class="brand-dot"></span>
      <span class="brand-name">Ironhold Security Systems Inc.</span>
    </div>
    <p class="website">www.ironholdsecuritysystemsinc.com</p>
    <span class="gold-rule"></span>
  </section>
</main>
</body>
</html>
```